Business Card Design for company

We want new business cards. We'd like something different-- yet still highly professional. Our tagline is Providing leadership, delivering success. Stock photos are ok, as long as they are relevant and look upscale.

Target Market(s)

Architecture/Business Management Consulting/Engineering Consulting

Contact Information for Business Card

dark gray background with pops of blue might be good, but you tell me. You're the designers. Rounded corners might be nice, but again, you tell me.

Font styles to use
Serif
Sans Serif

Colors
3276b5
5c5c5c
9d9d9d
fbfbfb

Requirements
Nice to have
• Something different, but still very professional.

```html
<!DOCTYPE html>
<html lang="en">
<head>
<meta charset="utf-8">
<title>Velmark International – Business Card</title>
<link href="https://fonts.googleapis.com/css2?family=Montserrat:wght@600&family=Work+Sans:wght@400;500&display=swap" rel="stylesheet">
<style>
  :root{
    --brand-blue:#2a6096;
    --accent-blue:#1f5a93;
    --ink:#4a4a4a;
    --ink-dark:#3a3f47;
    --muted:#7a7a7a;
    --paper:#fbfbfb;
    --backdrop:#b9b9b9;
  }
  *{box-sizing:border-box;margin:0;padding:0}
  html,body{width:1200px;height:930px;overflow:hidden}
  body{background:var(--backdrop);position:relative;font-family:"Work Sans",sans-serif}
  .card{position:absolute;width:560px;height:320px;border-radius:22px;overflow:hidden;box-shadow:0 4px 10px rgba(0,0,0,.25)}

  /* front */
  .card-front{left:100px;top:90px;background:var(--brand-blue);color:var(--paper)}
  .card-front .wordmark{position:absolute;left:0;right:0;top:92px;text-align:center;font-family:"Montserrat",sans-serif;font-weight:600;color:var(--paper);line-height:1.15}
  .card-front .wordmark .w1{display:block;font-size:52px;letter-spacing:2px}
  .card-front .wordmark .w2{display:block;font-size:22px;letter-spacing:3px}
  .card-front .web-rule{position:absolute;left:90px;right:90px;top:250px;display:flex;align-items:center;gap:12px;font-size:14px;letter-spacing:.5px}
  .card-front .web-rule::before,.card-front .web-rule::after{content:"";flex:1;height:1px;background:rgba(251,251,251,.7)}

  /* back */
  .card-back{left:540px;top:510px;background:var(--paper);color:var(--ink)}
  .card-back .wordmark{position:absolute;left:34px;top:70px;font-family:"Montserrat",sans-serif;font-weight:600;color:var(--brand-blue);line-height:1.15}
  .card-back .wordmark .w1{display:block;font-size:40px;letter-spacing:1.5px}
  .card-back .wordmark .w2{display:block;font-size:16px;letter-spacing:2.5px}
  .holder{position:absolute;right:34px;top:42px;text-align:right;width:250px}
  .holder .name{font-size:22px;font-weight:500;color:var(--accent-blue);letter-spacing:.5px}
  .holder .role{font-size:12px;color:var(--ink);margin-top:2px;padding-bottom:8px;border-bottom:1.5px solid var(--accent-blue)}
  .address{position:absolute;right:34px;top:128px;text-align:right;font-size:13px;line-height:1.6;color:var(--ink)}
  .contacts{position:absolute;left:34px;right:260px;top:198px;border-top:1.5px solid var(--accent-blue);padding-top:12px;list-style:none}
  .contacts li{display:flex;align-items:center;gap:10px;font-size:14px;line-height:1.75;color:var(--ink-dark);white-space:nowrap}
  .contacts svg{width:11px;height:11px;fill:var(--accent-blue);flex:none}
  .contacts .hl{color:var(--accent-blue)}
</style>
</head>
<body>
  <section class="card card-front" aria-label="Card front">
    <div class="wordmark"><span class="w1">VELMARK</span><span class="w2">INTERNATIONAL</span></div>
    <div class="web-rule">www.velmarkintl.com</div>
  </section>

  <section class="card card-back" aria-label="Card back">
    <div class="wordmark"><span class="w1">VELMARK</span><span class="w2">INTERNATIONAL</span></div>
    <div class="holder">
      <div class="name">DANIEL ARCHER</div>
      <div class="role">Director</div>
    </div>
    <div class="address">58b Harlow Street,<br>Ashford, NZ, 8024</div>
    <ul class="contacts">
      <li><svg viewBox="0 0 12 12"><path d="M2.5 1l2 2-1 1.5c.6 1.5 1.8 2.7 3.3 3.3L8.3 6.8l2 2-1.3 1.9C5 10.3 1.7 7 1.3 2.3z"/></svg>(514) 555-0142</li>
      <li><svg viewBox="0 0 12 12"><path d="M1 3h10v6H1zM2 4v.3l4 2.4 4-2.4V4zM2 5.5V8h8V5.5L6 8z" fill-rule="evenodd"/></svg>info@velmarkintl.com</li>
      <li><svg viewBox="0 0 12 12"><circle cx="6" cy="6" r="5"/></svg>www.<span class="hl">velmarkintl</span>.com</li>
    </ul>
  </section>
</body>
</html>
```